Coastline Premier Retreats Business Card Design

Design a business card for Coastline Premier Retreats. Look at the website for colors and reference. Card should have logo, name, title, office number, mobile number, email, URL and a tagline like, "Luxury Hotel & Resort Email Marketing" (This might change).

https://www.coastlinepremierretreats.example

The rest I will leave up to your imagination.

Contact Information for Business Card

Logo, name, title, office number, mobile number, email, URL and a tagline like, "Luxury Hotel & Resort Email Marketing" (This might change).

```html
<!DOCTYPE html>
<html lang="en">
<head>
<meta charset="utf-8">
<title>Coastline Premier Retreats – Business Card</title>
<link rel="stylesheet" href="https://fonts.googleapis.com/css2?family=Open+Sans:wght@400;600;700;800&display=swap">
<style>
  :root {
    --stage: #242424;
    --orange: #f37521;
    --card-dark: #1f1f23;
    --white: #ffffff;
    --muted: #e9e9e9;
  }
  * { box-sizing: border-box; margin: 0; padding: 0; }
  html, body {
    width: 1200px; height: 780px; overflow: hidden;
    background: var(--stage);
    font-family: "Open Sans", Arial, sans-serif;
  }
  .stage {
    position: relative; width: 1200px; height: 780px;
    display: flex; align-items: center; justify-content: center; gap: 40px;
  }
  .card {
    position: relative; width: 540px; height: 310px;
    border-radius: 18px; overflow: hidden;
    box-shadow: 0 12px 30px rgba(0,0,0,.45);
  }
  /* Wordmark: invented name, one colour, one weight */
  .wordmark {
    display: flex; align-items: center; gap: 14px;
    font-weight: 800; text-transform: uppercase; letter-spacing: .05em;
    line-height: 1.02; color: var(--white);
  }
  .wordmark__square { flex: none; background: var(--white); }
  .wordmark__text { display: block; }

  /* Front */
  .card--front {
    background: var(--orange);
    display: flex; align-items: center; justify-content: center;
  }
  .card--front .wordmark { font-size: 38px; gap: 18px; }
  .card--front .wordmark__square { width: 22px; height: 22px; }

  /* Back */
  .card--back { background: var(--card-dark); color: var(--white); }
  .card--back .wordmark {
    position: absolute; left: 30px; top: 30px; font-size: 22px;
  }
  .card--back .wordmark__square { width: 14px; height: 14px; background: var(--orange); }

  .identity {
    position: absolute; right: 0; top: 98px;
    display: flex; align-items: stretch; gap: 12px;
  }
  .identity__text { text-align: right; padding-top: 2px; }
  .identity__name { font-size: 26px; font-weight: 700; line-height: 1.1; }
  .identity__first { color: var(--orange); }
  .identity__title { font-size: 13px; color: var(--muted); margin-top: 4px; }
  .identity__bar { width: 14px; background: var(--orange); }

  .tagline {
    position: absolute; left: 52px; top: 158px;
    color: var(--orange); font-size: 13.5px; line-height: 1.35;
  }
  .contacts {
    position: absolute; left: 52px; top: 212px; list-style: none;
    font-size: 13px; line-height: 1;
  }
  .contacts li { display: flex; align-items: center; gap: 9px; height: 19px; }
  .contacts svg { width: 12px; height: 12px; flex: none; fill: var(--orange); }
</style>
</head>
<body>
<main class="stage">
  <section class="card card--front" aria-label="Card front">
    <div class="wordmark">
      <span class="wordmark__square"></span>
      <span class="wordmark__text">Coastline<br>Premier Retreats</span>
    </div>
  </section>

  <section class="card card--back" aria-label="Card back">
    <div class="wordmark">
      <span class="wordmark__square"></span>
      <span class="wordmark__text">Coastline<br>Premier Retreats</span>
    </div>

    <div class="identity">
      <div class="identity__text">
        <p class="identity__name"><span class="identity__first">Lena</span> Marovic</p>
        <p class="identity__title">Managing Director</p>
      </div>
      <span class="identity__bar"></span>
    </div>

    <p class="tagline">Luxury Hotel &amp;<br>Resort Email Marketing</p>

    <ul class="contacts">
      <li><svg viewBox="0 0 24 24" aria-hidden="true"><path d="M6.6 10.8a15 15 0 0 0 6.6 6.6l2.2-2.2a1 1 0 0 1 1-.25 11.4 11.4 0 0 0 3.6.57 1 1 0 0 1 1 1V20a1 1 0 0 1-1 1A17 17 0 0 1 3 4a1 1 0 0 1 1-1h3.5a1 1 0 0 1 1 1c0 1.25.2 2.45.57 3.57a1 1 0 0 1-.25 1z"/></svg>(555) 214-0387</li>
      <li><svg viewBox="0 0 24 24" aria-hidden="true"><path d="M7 1h10a2 2 0 0 1 2 2v18a2 2 0 0 1-2 2H7a2 2 0 0 1-2-2V3a2 2 0 0 1 2-2zm0 3v15h10V4zm5 16.2a1 1 0 1 0 0 .01z"/></svg>(555) 214-0922</li>
      <li><svg viewBox="0 0 24 24" aria-hidden="true"><path d="M12 2a10 10 0 1 0 0 20 10 10 0 0 0 0-20zm6.9 6h-3a15.7 15.7 0 0 0-1.4-3.6A8 8 0 0 1 18.9 8zM12 4c.8 1.2 1.5 2.5 1.9 4h-3.8c.4-1.5 1.1-2.8 1.9-4zM4.3 14a8.2 8.2 0 0 1 0-4h3.4a16.5 16.5 0 0 0 0 4zm.8 2h3a15.7 15.7 0 0 0 1.4 3.6A8 8 0 0 1 5.1 16zm3-8h-3a8 8 0 0 1 4.4-3.6A15.7 15.7 0 0 0 8.1 8zM12 20c-.8-1.2-1.5-2.5-1.9-4h3.8c-.4 1.5-1.1 2.8-1.9 4zm2.3-6H9.7a14.7 14.7 0 0 1 0-4h4.6a14.7 14.7 0 0 1 0 4zm.2 5.6a15.7 15.7 0 0 0 1.4-3.6h3a8 8 0 0 1-4.4 3.6zm1.8-5.6a16.5 16.5 0 0 0 0-4h3.4a8.2 8.2 0 0 1 0 4z"/></svg>www.coastlinepremierretreats.example</li>
      <li><svg viewBox="0 0 24 24" aria-hidden="true"><path d="M3 5h18a1 1 0 0 1 1 1v12a1 1 0 0 1-1 1H3a1 1 0 0 1-1-1V6a1 1 0 0 1 1-1zm1 2.4V17h16V7.4l-8 5.3z"/></svg>info@coastlinepremierretreats.example</li>
    </ul>
  </section>
</main>
</body>
</html>
```